Website development company website

ABOUT COMPANY
Hi everyone! We're a Melbourne, Australia website development company in a need of a website design that will make online store merchants want to engage our services.
We specialise exclusively in Torvista e-commerce platform (https://torvista-platform.example/). What distinguishes our business from competition is that rather than designing and building brand new websites, we offer development, support and maintenance services to established websites. Maintenance and Support are the keywords representing our business.
Our potential clients are people with broken, slow and underperforming Torvista installations who need assistance getting their websites up and making sales. Our website must pass the message that we can help, and provide quick means of making contact.
DESIGN
Overall, we're looking for a slick, clean, airy, conservative design. No need to do anything crazy, try to stick to what's "standard" in website design these days and make it easy on all of us. The website is unlikely to be updated too often so it needs to look attractive and fresh first time over and after a year, too.
Attached is our new logo, which you'll be able to take the basic idea from, the colors and fonts. Though, don't use the fonts from the logo in the website, stick to the standard widely supported fonts. Additional use of Google fonts is fine.
Don't overdo it with colors, stick to conservative basic color set and only use the colors from the log for accents like headings etc. Please, don't be tempted to use the blue and orange as background of whole blocks, other than perhaps footer. Thanks.
For the images used, I'd like to stay away from a design studio/digital agency feel and lean more towards professional support and maintenance services. I'm thinking images of content merchants doing their job. Something along the lines of "We'll be taking care of the website so that you only need to care about the business".
Some ideas I like:
http://www.plumframe-pics.example/detail/photo/portrait-of-confident-male-design-professional-royalty-free-image/572048163
http://www.plumframe-pics.example/detail/photo/designer-taking-picture-of-hat-high-res-stock-photography/839207514
http://www.plumframe-pics.example/detail/photo/woman-packaging-pottery-royalty-free-image/216684093
Images of colorful shopping bags and shopping carts are over the top and not serious enough. Instead of images matching Online Shopping, I'd try going more for Stability, Reliability, Performance.
Our existing website is http://www.bravuln.example. Please, don't take design ideas from it, but it will give you a picture of the structure of our new website and content that's going to be used initially.
If you could include a basic icon set to use throughout the website, that would be great. If the icons could match our logo (attached), it would be a big plus.
ALL PAGES
Every page must contain clearly visible phone number (1300 648 907) and a Contact Us Now button, which opens an AJAX driven popup form with Name, Email, Phone and Message to be sent through.
To start with, main menu items will be Torvista, Portfolio, Contact.
At the bottom of each page, please, include a newsletter subscription form with text Subscribe to Torvista Support and Security Updates.
For the footer, I'd like to see a logo strip with the following logos in grayscale (no need to link anywhere): Torvista, QRX, DataVane, NCB. You'll find the logos on Google Images.
Standard footer columns follow. Here, I'd like to see logos in color: Torvista Certified Developer, Torvista Ceritified Solution Provider. Again, the logos are on Google Images.
No social media logos/links necessary anywhere on the website.
...and then the copyright line.
FRONT PAGE
Large slider with images that would appeal to our target audience. Keywords here would be Torvista System Audit, Torvista Performance Optimisation, Torvista Website Emergency Recovery, Torvista Development Infrastructure Hosting. We'll have a static page created for each of these to link to.
In a corner of the slider, or on the edge, can I have an overlay with logos in color (same as footer): Torvista Certified Developer, Torvista Ceritified Solution Provider.
Underneath, a number of blocks, each with an image and teaser that we'll use to link to various pages throughout the website.
PORTFOLIO PAGE
I'm thinking a single long page with a block per client, which will contain project name, description from us and a testimonial from client. Also, each block will contain a single large screenshot. No gallery or slideshow is necessary here, just one image per project.
I'll leave the layout up to you, but try to put yourself in the shoes of a potential client reviewing our past work by simply scrolling down this one page.
CONTACT US PAGE
Separate page with the same form as above, phone number (1300 648 907), email address (support@kavreo.example), address (Suite 42, Level 3|8 Wattlebrook Lane|Fernvale Heights VIC 3999), and a grayscale Mapwell Map.
CODING UP
Coding up into static HTML/CSS/JS is equally important as the design itself. We're a website development company, we'll be integrating the theme. We will spot any issues and we will point them out.
Coded up design must be fully responsive. Enough said.
To be able to create any content in future, we'd like one extra page coded up with samples of all themed elements, lists, forms, buttons, 2, 3, 4-column layout, alerts, icons, etc. This page does not need to be designed, only coded up.
The design will be integrated into Drupal using Twig. If possible at all, try to keep it in mind when designing and coding up, and make the integration into a Drupal theme easier for us.
GOOD LUCK!
That's it. Let me know if anything needs clarifying. So far I've had a great experience with ArtFlockly. I don't doubt some great designs will emerge. Clever ideas are highly appreciated, but also make it clear you've read and followed the points in this brief. Cheers, Tom

```html
<!DOCTYPE html>
<html lang="en">
<head>
<meta charset="utf-8">
<title>Kavreo Commerce – Torvista Development, Support and Maintenance</title>
<link href="https://fonts.googleapis.com/css2?family=Open+Sans:wght@300;400;600;700;800&display=swap" rel="stylesheet">
<style>
:root{
  --navy:#1f4a7c;
  --orange:#f08a1c;
  --ink:#333333;
  --muted:#777777;
  --light-band:#ececec;
  --portfolio-bg:#ebebeb;
  --dark:#3b3b3b;
  --footer:#2b2b2b;
  --footer-base:#1f1f1f;
  --teal:#5ec4b6;
  --logo-grey:#a8a8a8;
  --white:#ffffff;
}
*{box-sizing:border-box;margin:0;padding:0}
html,body{width:1200px;height:2970px;overflow:hidden}
body{font-family:"Open Sans",Arial,sans-serif;color:var(--ink);background:var(--white);position:relative}
a{color:inherit;text-decoration:none}

/* Header */
.site-header{position:absolute;top:0;left:0;width:1200px;height:87px;background:var(--white);box-shadow:0 1px 4px rgba(0,0,0,.12);z-index:2}
.brand{position:absolute;left:130px;top:18px;display:flex;align-items:center;gap:8px}
.brand-mark{width:30px;height:36px;background:var(--orange);border-radius:3px}
.brand-name{font-size:28px;font-weight:700;color:var(--navy);letter-spacing:-.5px;line-height:1}
.main-nav{position:absolute;left:412px;top:0;height:87px;display:flex;align-items:center}
.main-nav a{font-size:13px;color:#555;position:relative;padding:0 17px;height:87px;display:flex;align-items:center}
.main-nav a+a::before{content:"";position:absolute;left:-2px;top:42px;width:4px;height:4px;border-radius:50%;background:#c5c5c5}
.main-nav a.is-active{color:var(--navy)}
.main-nav a.is-active::after{content:"";position:absolute;left:0;right:0;bottom:0;height:3px;background:var(--navy)}
.header-call{position:absolute;left:903px;top:16px;height:56px;border-left:1px solid #ddd;padding-left:24px;text-align:right;width:168px}
.header-call small{display:block;font-size:13px;color:#555}
.header-call strong{display:block;font-size:24px;font-weight:600;color:var(--orange);line-height:1.2;white-space:nowrap}

/* Hero */
.hero{position:absolute;top:87px;left:0;width:1200px;height:491px;background:linear-gradient(100deg,#c9d3dc 0%,#8e9cab 30%,#6b7a89 55%,#a5b1bd 80%,#d4dbe2 100%)}
.hero-title{position:absolute;top:158px;left:0;width:1200px;text-align:center}
.hero-title span{display:inline-block;background:rgba(50,50,50,.55);color:var(--white);font-weight:700;font-size:33px;letter-spacing:1px;padding:2px 16px;margin-bottom:8px}
.hero-actions{position:absolute;top:282px;left:0;width:1200px;display:flex;justify-content:center;gap:16px}
.btn{display:inline-flex;align-items:center;justify-content:center;font-size:14px;height:36px;padding:0 28px}
.btn-primary{background:var(--navy);color:var(--white)}
.btn-outline-light{border:2px solid var(--white);color:var(--white)}
.hero-arrow{position:absolute;top:222px;width:52px;height:52px;background:rgba(255,255,255,.35);display:flex;align-items:center;justify-content:center}
.hero-arrow.prev{left:0}.hero-arrow.next{right:0}

/* Tech strip */
.tech-strip{position:absolute;left:0;width:1200px;height:99px;display:flex;align-items:center;justify-content:space-between;padding:0 126px}
.tech-strip.top{top:578px;background:var(--light-band)}
.tech-strip.bottom{top:2487px;background:var(--white)}
.tech-strip span{font-size:30px;font-weight:600;color:var(--logo-grey);letter-spacing:-.5px}

/* Welcome */
.welcome{position:absolute;top:677px;left:0;width:1200px;height:483px;text-align:center}
.eyebrow{margin-top:34px;font-size:13px;color:#444}
.welcome h1{font-size:25px;font-weight:300;color:#333;line-height:1.38;margin-top:14px}
.welcome h1 strong{font-weight:400}
.feature-grid{position:absolute;top:178px;left:130px;width:940px;display:flex}
.feature-grid::after{content:"";position:absolute;left:470px;top:0;width:1px;height:212px;background:#ddd}
.feature{width:470px;padding:0 60px}
.feature svg{display:block;margin:0 auto 18px}
.feature h2{font-size:17px;font-weight:600;color:#222;margin-bottom:14px}
.feature p{font-size:11.5px;line-height:1.72;color:#666}

/* What we do */
.services{position:absolute;top:1160px;left:0;width:1200px;height:507px;background:linear-gradient(135deg,#444 0%,#383838 45%,#2f2f2f 100%);text-align:center}
.section-title{font-size:24px;font-weight:300}
.section-title strong{font-weight:600}
.services .section-title{color:var(--white);margin-top:32px}
.services .section-sub{color:#a8a8a8;font-size:13px;margin-top:8px}
.service-card{position:absolute;top:172px;width:293px;height:149px;background:var(--white);border-radius:2px;padding-top:60px}
.service-card .icon{position:absolute;top:-30px;left:106px;width:80px;height:80px;border-radius:50%;background:var(--teal);display:flex;align-items:center;justify-content:center}
.service-card h3{font-size:17px;font-weight:600;color:#222}
.service-card p{font-size:11.5px;color:#777;line-height:1.7;padding:0 24px;margin-top:6px}
.service-card .btn-ghost{display:inline-block;margin-top:10px;background:#eee;color:#aaa;font-size:10.5px;padding:4px 16px}
.services .tagline{position:absolute;top:408px;width:1200px;font-size:12.5px;color:#aaa}
.services .btn-outline-light{position:absolute;top:442px;left:518px;width:164px;height:34px;padding:0;font-size:13px}

/* Testimonials */
.testimonials{position:absolute;top:1667px;left:0;width:1200px;height:313px;text-align:center}
.testimonials .section-title{color:#333;margin-top:36px}
.section-sub{font-size:13px;color:#555;margin-top:8px}
.testimonial{position:absolute;top:155px;left:133px;width:940px;display:flex;text-align:left}
.testimonial-photo{width:110px;height:110px;border-radius:50%;background:radial-gradient(circle at 50% 40%,#c8b8a8,#556477 70%,#2d3a4d);flex:none}
.testimonial blockquote{margin-left:36px;border-left:1px solid #ddd;padding-left:36px;font-size:13.5px;line-height:1.95;color:#444}
.testimonial cite{display:block;font-style:normal;margin-top:10px;color:var(--orange);font-weight:600;font-size:14px}
.testimonial cite span{color:#888;font-weight:400}

/* Portfolio */
.portfolio{position:absolute;top:1980px;left:0;width:1200px;height:507px;background:var(--portfolio-bg);text-align:center}
.portfolio .section-title{color:#333;margin-top:36px}
.project{position:absolute;top:135px;width:210px;height:241px;background:var(--white);box-shadow:0 1px 3px rgba(0,0,0,.12)}
.project-shot{height:198px}
.project p{font-size:13px;color:#444;line-height:43px}
.shot-1{background:linear-gradient(180deg,#2f74b5 0%,#8fb3d4 40%,#e4e9ee 100%)}
.shot-2{background:linear-gradient(180deg,#e9e9e9 0%,#c23a3a 55%,#f2f2f2 100%)}
.shot-3{background:linear-gradient(180deg,#3aa6d8 0%,#bfe3f2 40%,#f4f4f4 100%)}
.shot-4{background:linear-gradient(180deg,#2c89c3 0%,#dfe9f1 45%,#f5f5f5 100%)}
.carousel-arrow{position:absolute;top:232px}
.carousel-arrow.prev{left:56px}.carousel-arrow.next{left:1124px}
.btn-outline-dark{position:absolute;top:424px;left:519px;width:162px;height:34px;border:1px solid #999;color:#666;font-size:13px;display:flex;align-items:center;justify-content:center}

/* Footer */
.site-footer{position:absolute;top:2586px;left:0;width:1200px;height:325px;background:var(--footer);color:#cfcfcf}
.footer-col{position:absolute;top:56px}
.footer-col h4{font-size:17px;font-weight:600;color:var(--white);margin-bottom:26px}
.footer-links li{list-style:none;font-size:12px;line-height:27px}
.footer-col p{font-size:12px;line-height:1.8}
.newsletter-input{margin-top:22px;width:232px;height:34px;background:#3f3f3f;display:flex;align-items:center;padding-left:10px;gap:8px;font-size:11px;color:#777}
.btn-orange{margin-top:14px;background:var(--orange);color:var(--white);font-weight:600;font-size:14px;width:110px;height:34px;display:flex;align-items:center;justify-content:center}
.footer-map{position:absolute;top:50px;left:794px;width:273px;height:156px;background:linear-gradient(135deg,#6a6a6a,#4f4f4f 60%,#5e5e5e)}
.map-link{position:absolute;top:214px;left:797px;font-size:12px;text-decoration:underline;color:#cfcfcf}
.footer-base{position:absolute;top:2911px;left:0;width:1200px;height:59px;background:var(--footer-base);color:#aaa;font-size:12px;display:flex;align-items:center;justify-content:center}
</style>
</head>
<body>

<header class="site-header">
  <a class="brand" href="#"><span class="brand-mark"></span><span class="brand-name">Kavreo Commerce</span></a>
  <nav class="main-nav">
    <a href="#" class="is-active">Home</a>
    <a href="#">About Us</a>
    <a href="#">Torvista</a>
    <a href="#">Our Portfolio</a>
    <a href="#">Contact Us</a>
  </nav>
  <div class="header-call"><small>Call Us Now!</small><strong>1300 648 907</strong></div>
</header>

<section class="hero" role="img" aria-label="Smiling businessman in a shirt and tie shaking hands with a colleague in a bright office">
  <h2 class="hero-title"><span>HIGH PERFORMANCE TORVISTA SITES</span><br><span>ON TIME AND ON BUDGET.</span></h2>
  <div class="hero-actions"><a class="btn btn-primary" href="#">Read More</a><a class="btn btn-outline-light" href="#">Contact Us</a></div>
  <a class="hero-arrow prev" href="#" aria-label="Previous slide"><svg width="14" height="22" viewBox="0 0 14 22"><path d="M11 2 3 11l8 9" fill="none" stroke="#fff" stroke-width="3"/></svg></a>
  <a class="hero-arrow next" href="#" aria-label="Next slide"><svg width="14" height="22" viewBox="0 0 14 22"><path d="M3 2l8 9-8 9" fill="none" stroke="#fff" stroke-width="3"/></svg></a>
</section>

<div class="tech-strip top"><span>Hypermark</span><span>Torvista</span><span>Kopi</span><span>QRX</span><span>NCB</span><span>DataVane</span></div>

<section class="welcome">
  <p class="eyebrow">Welcome to Kavreo Commerce</p>
  <h1>New generation websites by <strong>new generation designers.</strong><br>For new generation entrepreneurs..</h1>
  <div class="feature-grid">
    <div class="feature">
      <svg width="64" height="52" viewBox="0 0 64 52"><rect x="4" y="3" width="56" height="38" rx="2" fill="none" stroke="#f08a1c" stroke-width="3"/><path d="M1 47h62" stroke="#f08a1c" stroke-width="3"/><path d="M24 15l-7 7 7 7M40 15l7 7-7 7M35 13l-6 18" fill="none" stroke="#f08a1c" stroke-width="2.5"/></svg>
      <h2>Torvista Certified Developer</h2>
      <p>It is a long established fact that a reader will be distracted by the readable content of a page when looking at its layout. The point of using Lorem Ipsum is that it has a more-or-less normal distribution of letters, as opposed to using , making it look like readable English.</p>
    </div>
    <div class="feature">
      <svg width="64" height="64" viewBox="0 0 64 64" style="margin-top:-12px;margin-bottom:18px"><path d="M32 14a14 14 0 0 0-8 25.5V46h16v-6.5A14 14 0 0 0 32 14z" fill="none" stroke="#f08a1c" stroke-width="3"/><path d="M25 51h14M27 56h10M32 2v6M12 10l4 4M52 10l-4 4M4 30h6M54 30h6" stroke="#f08a1c" stroke-width="3" stroke-linecap="round"/></svg>
      <h2>Torvista Certified Solution Provider</h2>
      <p>It is a long established fact that a reader will be distracted by the readable content of a page when looking at its layout. The point of using Lorem Ipsum is that it has a more-or-less normal distribution of letters, as opposed to using , making it look like readable English.</p>
    </div>
  </div>
</section>

<section class="services">
  <h2 class="section-title">What <strong>We Do</strong></h2>
  <p class="section-sub">Simply dummy text of the printing and typesetting industry.</p>
  <article class="service-card" style="left:131px">
    <div class="icon"><svg width="40" height="34" viewBox="0 0 40 34"><rect x="2" y="2" width="36" height="24" rx="2" fill="#fff"/><path d="M14 30h12" stroke="#fff" stroke-width="3"/><path d="M16 9l-4 5 4 5M24 9l4 5-4 5" fill="none" stroke="#e0533d" stroke-width="2.2"/></svg></div>
    <h3>Web Development</h3>
    <p>It is a long established fact that a reader will be distracted the readable content.</p>
    <a class="btn-ghost" href="#">Read More</a>
  </article>
  <article class="service-card" style="left:453px">
    <div class="icon" role="img" aria-label="Support agent wearing a headset" style="background:radial-gradient(circle,#f3d7b8 0%,#e9a55c 60%,#5ec4b6 62%)"></div>
    <h3>Web Support</h3>
    <p>It is a long established fact that a reader will be distracted the readable content.</p>
    <a class="btn-ghost" href="#">Read More</a>
  </article>
  <article class="service-card" style="left:774px">
    <div class="icon"><svg width="40" height="40" viewBox="0 0 40 40"><path d="M8 32 28 12" stroke="#fff" stroke-width="5" stroke-linecap="round"/><circle cx="30" cy="10" r="6" fill="none" stroke="#fff" stroke-width="3"/><path d="M10 8l22 24" stroke="#f08a1c" stroke-width="5" stroke-linecap="round"/></svg></div>
    <h3>Web Maintenance</h3>
    <p>It is a long established fact that a reader will be distracted the readable content.</p>
    <a class="btn-ghost" href="#">Read More</a>
  </article>
  <p class="tagline">High performance Torvista sites on time and on budget.</p>
  <a class="btn btn-outline-light" href="#">Contact Us Now!</a>
</section>

<section class="testimonials">
  <h2 class="section-title">Client <strong>Testimonials</strong></h2>
  <p class="section-sub">What our Customers say About us and Reviews</p>
  <div class="testimonial">
    <div class="testimonial-photo" role="img" aria-label="Portrait of a client in a suit and tie"></div>
    <blockquote>" Lorem Ipsum is simply dummy text of the printing and typesetting industry. Lorem Ipsum has been the industry's standard dummy text ever since the 1500s, when an unknown printer took a galley of type and scrambled it to make a type specimen book. It has survived not only five centuries "
      <cite>Daniel Ferrow, <span>USA</span></cite>
    </blockquote>
  </div>
</section>

<section class="portfolio">
  <h2 class="section-title">Our <strong>Portfolio</strong></h2>
  <p class="section-sub">Simply dummy text of the printing and typesetting industry.</p>
  <svg class="carousel-arrow prev" width="20" height="60" viewBox="0 0 20 60"><path d="M18 2 2 30l16 28" fill="none" stroke="#777" stroke-width="1.5"/></svg>
  <article class="project" style="left:131px"><div class="project-shot shot-1" role="img" aria-label="Screenshot of a medical clinic website"></div><p>Our project name 01</p></article>
  <article class="project" style="left:372px"><div class="project-shot shot-2" role="img" aria-label="Screenshot of a creative design studio website"></div><p>Our project name 02</p></article>
  <article class="project" style="left:616px"><div class="project-shot shot-3" role="img" aria-label="Screenshot of a wedding photography website"></div><p>Our project name 03</p></article>
  <article class="project" style="left:857px"><div class="project-shot shot-4" role="img" aria-label="Screenshot of a travel resort website"></div><p>Our project name 04</p></article>
  <svg class="carousel-arrow next" width="20" height="60" viewBox="0 0 20 60"><path d="M2 2l16 28L2 58" fill="none" stroke="#777" stroke-width="1.5"/></svg>
  <a class="btn-outline-dark" href="#">View More</a>
</section>

<div class="tech-strip bottom"><span>Hypermark</span><span>Torvista</span><span>Kopi</span><span>QRX</span><span>NCB</span><span>DataVane</span></div>

<footer class="site-footer">
  <div class="footer-col" style="left:131px">
    <h4>Quick Links</h4>
    <ul class="footer-links"><li>- Home</li><li>- About Us</li><li>- Torvista</li><li>- Our Portfolio</li><li>- Contact Us</li></ul>
  </div>
  <div class="footer-col" style="left:287px">
    <h4>Sign Up Newsletter</h4>
    <p>Simply dummy text of the printing and<br>typesetting industry.</p>
    <div class="newsletter-input"><svg width="14" height="10" viewBox="0 0 14 10"><rect width="14" height="10" fill="#ddd"/><path d="M0 0l7 6 7-6" fill="none" stroke="#3f3f3f" stroke-width="1.2"/></svg>Email Address</div>
    <a class="btn-orange" href="#">Submit</a>
  </div>
  <div class="footer-col" style="left:562px">
    <h4>Contact Us</h4>
    <p>Suite 42, Level 3, 8 Wattlebrook Lane,<br>Fernvale Heights VIC 3999</p>
    <p style="margin-top:8px">Phone:<br>1300 648 907</p>
    <p style="margin-top:8px">Email:<br>info@kavreo.example</p>
  </div>
  <div class="footer-map" role="img" aria-label="Greyscale street map with a location pin on the office">
    <svg width="273" height="156" viewBox="0 0 273 156"><path d="M136 52a14 14 0 0 0-14 14c0 11 14 26 14 26s14-15 14-26a14 14 0 0 0-14-14z" fill="#eee"/><circle cx="136" cy="66" r="5" fill="#5a5a5a"/></svg>
  </div>
  <a class="map-link" href="#">View Mapwell Map</a>
</footer>
<div class="footer-base">Copyright © 2016 - Kavreo Commerce, All Rights Reserved</div>

</body>
</html>
```